The Linen Loft Co

We need a business card design for our wardrobe company.
Please visit our website www.gentlelinenlofts.com to get an idea of who we are.

```html
<!DOCTYPE html>
<html lang="en">
<head>
<meta charset="utf-8">
<title>The Linen Loft Co — Business Card</title>
<link href="https://fonts.googleapis.com/css2?family=Montserrat:wght@500;600&family=Oswald:wght@500&family=Roboto:wght@400&display=swap" rel="stylesheet">
<style>
  :root {
    --backdrop: #1b1b1b;
    --card: #151515;
    --card-light: #2a2a2a;
    --ink: #f2f2f2;
    --ink-soft: #d6d6d6;
  }
  * { box-sizing: border-box; margin: 0; padding: 0; }
  html, body { width: 1200px; height: 900px; overflow: hidden; }
  body {
    background: var(--backdrop);
    position: relative;
    font-family: "Roboto", sans-serif;
    color: var(--ink);
  }
  .card {
    position: absolute;
    left: 260px;
    width: 680px;
    height: 388px;
    background: linear-gradient(135deg, var(--card) 0%, var(--card) 45%, var(--card-light) 100%);
    box-shadow: 0 10px 30px rgba(0,0,0,0.6);
  }
  .card--front { top: 42px; }
  .card--back { top: 470px; }

  .brand {
    position: absolute;
    left: 200px;
    top: 150px;
    display: flex;
    align-items: center;
    gap: 22px;
  }
  .brand__mark {
    width: 70px;
    height: 70px;
    border: 2px solid var(--ink);
  }
  .brand__name {
    font-family: "Montserrat", sans-serif;
    font-weight: 600;
    font-size: 19px;
    letter-spacing: 0.5px;
    text-transform: uppercase;
  }
  .brand__tagline {
    font-family: "Montserrat", sans-serif;
    font-weight: 500;
    font-size: 16px;
    margin-top: 6px;
    margin-left: 16px;
    color: var(--ink-soft);
  }

  .person {
    position: absolute;
    right: 385px;
    top: 132px;
    text-align: right;
  }
  .person__name {
    font-family: "Oswald", sans-serif;
    font-weight: 500;
    font-size: 40px;
    letter-spacing: 1px;
    text-transform: uppercase;
    line-height: 1.1;
  }
  .person__role { font-size: 19px; color: var(--ink-soft); margin-top: 2px; }

  .divider {
    position: absolute;
    left: 318px;
    top: 150px;
    width: 2px;
    height: 70px;
    background: var(--ink);
  }

  .contacts {
    position: absolute;
    left: 348px;
    top: 146px;
    list-style: none;
    font-size: 19px;
    letter-spacing: 0.5px;
  }
  .contacts li { display: flex; align-items: center; gap: 10px; height: 26px; }
  .contacts svg { width: 14px; height: 14px; flex: none; }

  .address {
    position: absolute;
    left: 0;
    right: 0;
    bottom: 42px;
    text-align: center;
    font-size: 19px;
    letter-spacing: 0.5px;
  }
</style>
</head>
<body>
  <section class="card card--front">
    <div class="brand">
      <div class="brand__mark"></div>
      <div class="brand__text">
        <div class="brand__name">The Linen Loft Co</div>
        <div class="brand__tagline">Folded with Quiet Care</div>
      </div>
    </div>
  </section>

  <section class="card card--back">
    <div class="person">
      <div class="person__name">Daniel Harper</div>
      <div class="person__role">Director</div>
    </div>
    <div class="divider"></div>
    <ul class="contacts">
      <li>
        <svg viewBox="0 0 16 16" fill="none" stroke="#f2f2f2" stroke-width="1.5" aria-hidden="true"><path d="M4 1.5l2.2 3-1.4 1.6c.8 2 2.3 3.5 4.3 4.4l1.6-1.4 3 2.2-1.2 2.4C7.6 13.5 2.5 8.4 2 3z"/></svg>
        <span>0207 946 0321</span>
      </li>
      <li>
        <svg viewBox="0 0 16 16" fill="none" stroke="#f2f2f2" stroke-width="1.5" aria-hidden="true"><rect x="1.5" y="3.5" width="13" height="9"/><path d="M1.5 3.5L8 9l6.5-5.5"/></svg>
        <span>info@gentlelinenlofts.com</span>
      </li>
      <li>
        <svg viewBox="0 0 16 16" fill="none" stroke="#f2f2f2" stroke-width="1.3" aria-hidden="true"><circle cx="8" cy="8" r="6.5"/><ellipse cx="8" cy="8" rx="2.8" ry="6.5"/><path d="M1.5 8h13M2.5 4.8h11M2.5 11.2h11"/></svg>
        <span>www.gentlelinenlofts.com</span>
      </li>
    </ul>
    <p class="address">Orchard House, 42 Mill Lane, London N1 7QR</p>
  </section>
</body>
</html>
```